Website for 3d printing & other services

Hi, i'm after a website to sell my 3d printed automotive parts as well as sell my 3d printing services & other services.

There's a few things i need the website to have:

- Automatic 3d print quoting based on the file the client uploads to the website.
- Shop function where i can sell my custom automotive parts
- 3D printing technologies offered are SLA & FDM
- My business can offer 3d printing, 3d scanning, 3d cad design, cnc machining, steel fabrication, drafting services.

The color design is to suit my logo which is Black, orange & white.

Target Market(s)

3d printing, automotive, fabrication

Industry/Entity Type

General manufacturing & Custom automotive parts

Coding

Coded - Design and coding required

Number of Pages Required

5+ page

Requirements
Must have
• Automatic 3d print quoting. Shop for my printed parts.

```html
<!DOCTYPE html>
<html lang="en">
<head>
<meta charset="utf-8">
<title>KVR Draft &amp; Design — 3D Printed Automotive Parts</title>
<link rel="stylesheet" href="https://fonts.googleapis.com/css2?family=Poppins:ital,wght@0,400;0,500;0,600;0,700;0,800;0,900;1,400&display=swap">
<style>
:root{
  --ink:#05051a;
  --ink-2:#0b0b22;
  --orange:#ff7306;
  --orange-2:#f06a00;
  --white:#ffffff;
  --grey:#b9b9c4;
  --line:#3a3a4a;
}
*{box-sizing:border-box;margin:0;padding:0}
html,body{width:1200px;height:3285px;overflow:hidden}
body{position:relative;background:var(--ink);font-family:"Poppins",sans-serif;color:var(--white)}
.abs{position:absolute}
.btn{position:absolute;display:flex;align-items:center;justify-content:center;border-radius:30px;background:var(--orange);color:var(--white);font-weight:700;text-transform:uppercase}
.accent{color:var(--orange)}

/* header */
.site-header{left:0;top:0;width:1200px;height:143px;background:var(--ink)}
.site-header::after{content:"";position:absolute;left:0;bottom:0;width:100%;height:6px;background:#000}
.brand{left:143px;top:40px;width:170px}
.brand-name{font-size:44px;font-weight:800;color:var(--orange);letter-spacing:1px;line-height:1}
.brand-sub{font-size:15px;font-weight:600;color:var(--white);margin-top:8px;letter-spacing:.5px}
.search{left:673px;top:23px;width:305px;height:50px;border:2px solid #555a66;border-radius:26px;padding-left:24px;display:flex;align-items:center;font-size:13px;color:#e0e0e6}
.search-btn{position:absolute;right:7px;top:8px;width:32px;height:32px;border-radius:50%;background:var(--orange)}
.nav{left:463px;top:100px;font-size:14px;font-weight:700}
.nav a{color:var(--white);text-decoration:none;position:absolute;white-space:nowrap}
.nav .active::before{content:"";position:absolute;left:2px;top:-14px;width:9px;height:10px;background:var(--orange)}
.cart{left:1013px;top:88px}

/* hero */
.hero{left:0;top:143px;width:1200px;height:538px;background:linear-gradient(115deg,#1fa4d8 0%,#2786c9 35%,#3b4ea8 62%,#8452c9 85%,#9c6ad8 100%);overflow:hidden}
.hero-title{left:143px;top:93px;font-size:58px;font-weight:900;line-height:67px;text-transform:uppercase}
.hero .btn{left:142px;top:322px;width:154px;height:46px;font-size:14px}
.dots{left:575px;top:489px;display:flex;gap:10px}
.dots span{width:10px;height:10px;border-radius:50%;background:var(--white)}
.dots span.on{background:var(--orange)}
.quote{left:740px;top:64px;width:316px;height:402px;background:var(--white);border:2px solid var(--orange)}
.quote h2{position:absolute;left:0;top:26px;width:100%;text-align:center;color:#111;font-size:29px;font-weight:800}
.field{position:absolute;left:28px;width:258px;border:3px solid #e4e4e8;border-radius:28px;color:#777;font-size:13px;padding:16px 26px;box-shadow:inset 0 2px 3px rgba(0,0,0,.06)}
.quote .btn{left:96px;top:320px;width:122px;height:46px;font-size:14px}

/* parts */
.section-title{width:1200px;left:0;text-align:center;font-weight:900;text-transform:uppercase}
.parts-title{top:770px;font-size:51px;line-height:58px}
.part{top:939px;width:290px;height:316px;border:2px solid #4b4b58}
.part-photo{position:absolute;left:13px;top:15px;width:262px;height:183px}
.part-name{position:absolute;left:31px;top:229px;font-size:14px;font-weight:700}
.part-price{position:absolute;right:31px;top:225px;font-size:20px;font-weight:700;color:var(--orange)}
.part .btn{left:31px;top:261px;width:84px;height:31px;font-size:9px}
.more{left:500px;top:1302px;width:199px;height:46px;font-size:14px}

/* technologies */
.tech{top:1425px;width:600px;height:412px;overflow:hidden}
.tech-sla{left:0;background:linear-gradient(135deg,#ff7a10,#e56000 60%,#f27012)}
.tech-fdm{left:600px;background:linear-gradient(135deg,#5a5a60,#2e2e33 55%,#3f3f44)}
.tech h3{position:absolute;left:147px;top:57px;font-size:50px;font-weight:900;line-height:1}
.tech-fdm h3{left:51px}
.tech p{position:absolute;left:147px;top:122px;width:407px;font-size:13px;line-height:24px;text-align:justify}
.tech-fdm p{left:51px}
.tech .btn{top:298px;width:133px;height:47px;font-size:14px}
.tech-sla .btn{left:147px;background:var(--ink)}
.tech-fdm .btn{left:51px}

/* services */
.services-title{top:1935px;font-size:50px}
.service{top:2098px;width:291px;height:324px;border:2px solid var(--orange);border-radius:95px}
.service-photo{position:absolute;left:70px;top:-62px;width:150px;height:150px;border-radius:50%;border:4px solid var(--ink)}
.service h4{position:absolute;left:0;top:118px;width:100%;text-align:center;color:var(--orange);font-size:20px;font-weight:600}
.service p{position:absolute;left:0;top:165px;width:100%;text-align:center;font-size:13px;line-height:24px;white-space:nowrap}
.service svg.down{position:absolute;left:129px;top:276px}
.arrow{top:2247px}

/* reviews */
.reviews{left:0;top:2515px;width:1200px;height:410px;background:linear-gradient(180deg,#ff7a0c,#f06800 55%,#e25f00)}
.reviews h2{position:absolute;left:0;top:55px;width:100%;text-align:center;font-size:49px;font-weight:900}
.quote-mark{position:absolute;left:0;top:150px;width:100%;text-align:center;font-size:34px;font-weight:800;line-height:1}
.reviews blockquote{position:absolute;left:224px;top:194px;width:752px;font-style:italic;font-size:15.5px;line-height:26px;text-align:justify;text-align-last:center}
.reviewer{position:absolute;left:452px;top:310px;display:flex;align-items:center;gap:16px;font-size:22px;font-weight:800}
.stars{display:flex;gap:8px}

/* footer */
.site-footer{left:0;top:2925px;width:1200px;height:360px;background:var(--ink)}
.foot-links a{position:absolute;color:var(--white);text-decoration:none;font-size:14px;font-weight:700}
.foot-brand{left:510px;top:90px;text-align:center;width:175px}
.foot-brand .brand-name{font-size:50px}
.foot-brand .brand-sub{font-size:18px}
.contact{left:784px;display:flex;align-items:center;gap:16px;font-size:14px}
.contact i{width:42px;height:42px;border-radius:50%;border:2px solid #c9c9d2;display:flex;align-items:center;justify-content:center}
.social{left:148px;top:266px;display:flex;gap:14px}
.social span{width:47px;height:47px;border-radius:50%;border:2px solid var(--white)}
.social span.on{background:var(--orange);border-color:var(--orange)}
.legal{right:144px;top:281px;font-size:14px}
</style>
</head>
<body>

<header class="abs site-header">
  <div class="abs brand">
    <div class="brand-name">KVR</div>
    <div class="brand-sub">DRAFT &amp; DESIGN</div>
  </div>
  <div class="abs search">Search
    <span class="search-btn"><svg width="32" height="32" viewBox="0 0 32 32"><circle cx="15" cy="15" r="7" fill="none" stroke="#fff" stroke-width="2.4"/><path d="M20 20l4 4" stroke="#fff" stroke-width="2.4" stroke-linecap="round"/></svg></span>
  </div>
  <nav class="abs nav">
    <a class="active" style="left:0">HOME</a>
    <a style="left:72px">ABOUT</a>
    <a style="left:159px">PRODUCTS</a>
    <a style="left:266px">SERVICES</a>
    <a style="left:363px">NEWS</a>
    <a style="left:442px">CONTACT</a>
  </nav>
  <svg class="abs cart" width="46" height="40" viewBox="0 0 46 40" fill="none" stroke="#ff7306" stroke-width="3" stroke-linecap="round" stroke-linejoin="round">
    <path d="M2 6h6l5 22h24l5-16H15"/><circle cx="17" cy="35" r="2.5"/><circle cx="33" cy="35" r="2.5"/><path d="M28 2v12M22 8h12"/>
  </svg>
</header>

<section class="abs hero">
  <div class="abs" role="img" aria-label="Close-up photo of a 3D printed gear set in blue and red light" style="left:300px;top:40px;width:700px;height:500px;border-radius:50%;background:radial-gradient(circle at 45% 50%,rgba(200,40,60,.45),rgba(20,80,140,.35) 45%,transparent 70%)"></div>
  <h1 class="abs hero-title"><span class="accent">3D</span> PRINTED<br>AUTOMOTIVE<br>PARTS</h1>
  <a class="btn">GET STARTED</a>
  <form class="abs quote">
    <h2>GET A QUOTE</h2>
    <div class="field" style="top:85px;height:54px">Enter Name</div>
    <div class="field" style="top:146px;height:54px">Enter Email</div>
    <div class="field" style="top:207px;height:95px">Message</div>
    <a class="btn">SUBMIT</a>
  </form>
  <div class="abs dots"><span></span><span class="on"></span><span></span></div>
</section>

<h2 class="abs section-title parts-title">MY CUSTOM<br><span class="accent">AUTOMOTIVE PARTS</span></h2>

<article class="abs part" style="left:145px">
  <div class="part-photo" role="img" aria-label="Photo of assorted engine parts and pulleys" style="background:linear-gradient(135deg,#5d7288,#9fb0c0 45%,#3c4a58)"></div>
  <div class="part-name">NEMO ENIM IPSAM</div><div class="part-price">$56.34</div>
  <a class="btn">SHOP NOW</a>
</article>
<article class="abs part" style="left:456px">
  <div class="part-photo" role="img" aria-label="Photo of robotic arms on a production line" style="background:linear-gradient(135deg,#2d3848,#c27a3a 55%,#3a2e26)"></div>
  <div class="part-name">NEMO ENIM IPSAM</div><div class="part-price">$56.34</div>
  <a class="btn">SHOP NOW</a>
</article>
<article class="abs part" style="left:766px">
  <div class="part-photo" role="img" aria-label="Photo of small black machined parts laid out on a dark surface" style="background:linear-gradient(135deg,#2b2b2e,#3d3d41 50%,#1f1f22)"></div>
  <div class="part-name">NEMO ENIM IPSAM</div><div class="part-price">$56.34</div>
  <a class="btn">SHOP NOW</a>
</article>
<a class="btn more">VIEW MORE PARTS</a>

<section class="abs tech tech-sla" role="img" aria-label="Orange-toned photo of gears and spark plugs">
  <h3>SLA</h3>
  <p>Sed ut perspiciatis unde omnis iste natus error sit voluptatem accusantium doloremque laudantium, totam rem aperiam, eaque ipsa quae ab illo inventore veritatis et quasi architecto beatae vitae dicta sued ut perspiciatis unde omnis iste natus error sit voluptatem accusantium doloremque laudantium, totam rem aperiam, eaque ipsa quae ab</p>
  <a class="btn">READ MORE</a>
</section>
<section class="abs tech tech-fdm" role="img" aria-label="Grey-toned photo of machine gears">
  <h3>FDM</h3>
  <p>Sed ut perspiciatis unde omnis iste natus error sit voluptatem accusantium doloremque laudantium, totam rem aperiam, eaque ipsa quae ab illo inventore veritatis et quasi architecto beatae vitae dicta sued ut perspiciatis unde omnis iste natus error sit voluptatem accusantium doloremque laudantium, totam rem aperiam, eaque ipsa quae ab</p>
  <a class="btn">READ MORE</a>
</section>

<h2 class="abs section-title services-title">OUR <span class="accent">SERVICES</span></h2>

<svg class="abs arrow" style="left:80px" width="48" height="26" viewBox="0 0 48 26" fill="none" stroke="#fff" stroke-width="2.5" stroke-linecap="round"><path d="M46 13H3M13 3L3 13l10 10"/></svg>
<svg class="abs arrow" style="left:1072px" width="48" height="26" viewBox="0 0 48 26" fill="none" stroke="#fff" stroke-width="2.5" stroke-linecap="round"><path d="M2 13h43M35 3l10 10-10 10"/></svg>

<article class="abs service" style="left:144px">
  <div class="service-photo" role="img" aria-label="Photo of a grey 3D printed lattice part" style="background:radial-gradient(circle,#d8d8dc,#7c7c84)"></div>
  <h4>3D PRINTING</h4>
  <p>Sed ut perspiciatis unde omnis iste<br>natus error sit voluptatem ccusantium<br>doloremque laudantium, totam rem<br>aperiam, eaque ipsa quae ab illo</p>
  <svg class="down" width="30" height="30" viewBox="0 0 30 30" fill="none" stroke="#ff7306" stroke-width="2"><circle cx="15" cy="15" r="13"/><path d="M15 8v13M10 16l5 5 5-5"/></svg>
</article>
<article class="abs service" style="left:455px">
  <div class="service-photo" role="img" aria-label="Photo of a turbine part being 3D scanned" style="background:radial-gradient(circle,#b0203e,#4a1438 70%,#2a1030)"></div>
  <h4>3D SCANNING</h4>
  <p>Sed ut perspiciatis unde omnis iste<br>natus error sit voluptatem ccusantium<br>doloremque laudantium, totam rem<br>aperiam, eaque ipsa quae ab illo</p>
  <svg class="down" width="30" height="30" viewBox="0 0 30 30" fill="none" stroke="#ff7306" stroke-width="2"><circle cx="15" cy="15" r="13"/><path d="M15 8v13M10 16l5 5 5-5"/></svg>
</article>
<article class="abs service" style="left:766px">
  <div class="service-photo" role="img" aria-label="Screenshot of 3D CAD gear models" style="background:radial-gradient(circle at 65% 50%,#2f7ad8,#444a58 60%,#23262e)"></div>
  <h4>3D CAD DESIGN</h4>
  <p>Sed ut perspiciatis unde omnis iste<br>natus error sit voluptatem ccusantium<br>doloremque laudantium, totam rem<br>aperiam, eaque ipsa quae ab illo</p>
  <svg class="down" width="30" height="30" viewBox="0 0 30 30" fill="none" stroke="#ff7306" stroke-width="2"><circle cx="15" cy="15" r="13"/><path d="M15 8v13M10 16l5 5 5-5"/></svg>
</article>

<section class="abs reviews" role="img" aria-label="Orange-toned photo of a car engine bay">
  <h2>CUSTOMER REVIEWS</h2>
  <div class="quote-mark">&ldquo;</div>
  <svg class="abs" style="left:120px;top:230px" width="48" height="26" viewBox="0 0 48 26" fill="none" stroke="#fff" stroke-width="2.5" stroke-linecap="round"><path d="M46 13H3M13 3L3 13l10 10"/></svg>
  <svg class="abs" style="left:1032px;top:230px" width="48" height="26" viewBox="0 0 48 26" fill="none" stroke="#fff" stroke-width="2.5" stroke-linecap="round"><path d="M2 13h43M35 3l10 10-10 10"/></svg>
  <blockquote>"Sed ut perspiciatis unde omnis iste natus error sit voluptatem accusantium doloremque laudantium, totam rem aperiam, eaque ipsa quae ab illo inventore veritatis et quasi architecto beatae vitae dicta sunt explicabo. Nemo enim ipsam voluptatem quia voluptas sit aspernatur aut odit aut fugit, sed quia consequuntur magni dolores es"Sed ut perspiciatis unde omnis "</blockquote>
  <div class="reviewer">SAM RIVERA
    <div class="stars">
      <svg width="25" height="24" viewBox="0 0 24 23"><path fill="#ffd21a" d="M12 0l3.5 7.5 8.2.9-6.1 5.6 1.7 8.1L12 18l-7.3 4.1 1.7-8.1L.3 8.4l8.2-.9z"/></svg>
      <svg width="25" height="24" viewBox="0 0 24 23"><path fill="#ffd21a" d="M12 0l3.5 7.5 8.2.9-6.1 5.6 1.7 8.1L12 18l-7.3 4.1 1.7-8.1L.3 8.4l8.2-.9z"/></svg>
      <svg width="25" height="24" viewBox="0 0 24 23"><path fill="#ffd21a" d="M12 0l3.5 7.5 8.2.9-6.1 5.6 1.7 8.1L12 18l-7.3 4.1 1.7-8.1L.3 8.4l8.2-.9z"/></svg>
      <svg width="25" height="24" viewBox="0 0 24 23"><path fill="#ffd21a" d="M12 0l3.5 7.5 8.2.9-6.1 5.6 1.7 8.1L12 18l-7.3 4.1 1.7-8.1L.3 8.4l8.2-.9z"/></svg>
      <svg width="25" height="24" viewBox="0 0 24 23"><path fill="#ffd21a" d="M12 0l3.5 7.5 8.2.9-6.1 5.6 1.7 8.1L12 18l-7.3 4.1 1.7-8.1L.3 8.4l8.2-.9z"/></svg>
    </div>
  </div>
</section>

<footer class="abs site-footer">
  <nav class="foot-links">
    <a style="left:150px;top:92px">HOME</a>
    <a style="left:150px;top:130px">ABOUT</a>
    <a style="left:150px;top:168px">PRODUCTS</a>
    <a style="left:318px;top:92px">SERVICES</a>
    <a style="left:318px;top:130px">NEWS</a>
    <a style="left:318px;top:168px">CONTACT</a>
  </nav>
  <div class="abs foot-brand">
    <div class="brand-name">KVR</div>
    <div class="brand-sub">DRAFT &amp; DESIGN</div>
  </div>
  <div class="abs contact" style="top:72px">
    <i><svg width="18" height="14" viewBox="0 0 18 14" fill="none" stroke="#fff" stroke-width="1.8"><rect x="1" y="1" width="16" height="12" rx="1.5"/><path d="M1 2l8 6 8-6"/></svg></i>
    Email Us : info@kvrworks.com
  </div>
  <div class="abs contact" style="top:130px">
    <i><svg width="16" height="16" viewBox="0 0 24 24"><path fill="#fff" d="M6.6 10.8a15.1 15.1 0 006.6 6.6l2.2-2.2c.3-.3.7-.4 1-.2 1.1.4 2.3.6 3.6.6.6 0 1 .4 1 1V20c0 .6-.4 1-1 1A17 17 0 013 4c0-.6.4-1 1-1h3.5c.6 0 1 .4 1 1 0 1.3.2 2.5.6 3.6.1.3 0 .7-.2 1z"/></svg></i>
    Phone : +1 555 010 2040
  </div>
  <div class="abs social" aria-label="Social media links">
    <span aria-label="Social link"></span><span aria-label="Social link"></span><span class="on" aria-label="Social link"></span><span aria-label="Social link"></span>
  </div>
  <div class="abs legal">© Copyright 2023 KVR. All Rights Reserved &nbsp;| &nbsp;Privacy &nbsp;| &nbsp;Terms of use</div>
</footer>

</body>
</html>
```